Bramblewood Card Company Business Cards

We are a trading card store with Glimmorax, sports and other TCG cards, we need a business card design that encompasses a clean cut, modern style with a retro flare. website is bramblewoodcardco.com for reference. Can utilize a comic book era feel or a more modern outdoor feel to utilize the "Pacific Northwest" elements of tress, mountains, etc.

Industry/Entity Type

Trading cards and collectibles

Contact Information for Business Card

business name, email address, phone number, name, owner job title

Font styles to use
Sans Serif

```html
<!DOCTYPE html>
<html lang="en">
<head>
<meta charset="utf-8">
<title>Bramblewood Card Company — Business Cards</title>
<link rel="stylesheet" href="https://fonts.googleapis.com/css2?family=Montserrat:wght@400;500;700&display=swap">
<style>
  :root {
    --backdrop: #cfd3d4;
    --paper: #f7f8f8;
    --brand-blue: #13b3d8;
    --deep-blue: #1194b9;
    --charcoal: #3b3c3e;
    --ink: #2f3133;
    --rule: #c9cccd;
  }
  * { margin: 0; padding: 0; box-sizing: border-box; }
  html, body {
    width: 1200px; height: 829px; overflow: hidden;
    background: var(--backdrop);
    font-family: "Montserrat", sans-serif;
  }
  .stage {
    width: 1200px; height: 829px;
    display: flex; align-items: center; justify-content: center; gap: 40px;
  }
  .card {
    position: relative;
    width: 520px; height: 297px;
    border-radius: 3px;
    overflow: hidden;
    box-shadow: 0 10px 24px rgba(0,0,0,.18);
  }
  .card--front { background: var(--paper); }
  .card--back {
    background: var(--brand-blue);
    display: flex; align-items: center; justify-content: center;
  }
  .front-swoosh { position: absolute; left: 0; top: 0; width: 520px; height: 297px; }
  .brand {
    display: flex; align-items: center; gap: 10px;
    color: var(--charcoal); font-weight: 700; text-transform: uppercase;
  }
  .brand__mark { flex: none; background: var(--charcoal); }
  .card--front .brand {
    position: absolute; left: 34px; top: 74px; width: 190px;
    font-size: 17px; line-height: 1.2; letter-spacing: .5px;
  }
  .card--front .brand__mark { width: 16px; height: 16px; }
  .card--back .brand { font-size: 26px; line-height: 1.2; letter-spacing: 1px; width: 300px; }
  .card--back .brand__mark { width: 26px; height: 26px; border-radius: 50%; }
  .divider {
    position: absolute; left: 246px; top: 54px;
    width: 1px; height: 138px; background: var(--rule);
  }
  .contact {
    position: absolute; left: 268px; top: 52px;
    color: var(--ink); font-size: 12.5px; line-height: 1.45;
  }
  .contact__name {
    color: var(--brand-blue); font-weight: 700; font-size: 20px;
    letter-spacing: 1px; text-transform: uppercase; line-height: 1.1;
  }
  .contact__title { margin-bottom: 8px; }
  .contact__address { margin-bottom: 6px; }
  .contact__line { display: flex; align-items: center; gap: 7px; }
  .contact__icon { width: 10px; height: 10px; flex: none; }
</style>
</head>
<body>
<main class="stage">

  <section class="card card--front" aria-label="Business card front">
    <svg class="front-swoosh" viewBox="0 0 520 297" aria-hidden="true">
      <path d="M0 196 C 150 232, 330 270, 520 262 L520 297 L0 297 Z" fill="var(--deep-blue)"/>
      <path d="M0 186 C 150 226, 330 262, 520 256" fill="none" stroke="var(--charcoal)" stroke-width="5"/>
      <path d="M0 176 C 150 216, 330 250, 520 246" fill="none" stroke="var(--brand-blue)" stroke-width="3"/>
    </svg>

    <div class="brand">
      <span class="brand__mark"></span>
      <span class="brand__name">Bramblewood Card Company</span>
    </div>

    <div class="divider"></div>

    <div class="contact">
      <p class="contact__name">Dorian Vale</p>
      <p class="contact__title">CEO/Founder</p>
      <p class="contact__address">P.O. Box 3870 Ridge Rd<br>Cedar Falls WA 98231</p>
      <p class="contact__line">
        <svg class="contact__icon" viewBox="0 0 10 10" aria-hidden="true"><path d="M2 1 L4 3 L3 4 Q4 6 6 7 L7 6 L9 8 L8 9 Q3 9 1 2 Z" fill="var(--brand-blue)"/></svg>
        (555) 014 2286
      </p>
      <p class="contact__line">
        <svg class="contact__icon" viewBox="0 0 10 10" aria-hidden="true"><rect x="0.5" y="2" width="9" height="6" fill="var(--brand-blue)"/><path d="M0.5 2 L5 5.5 L9.5 2" fill="none" stroke="#fff" stroke-width="0.8"/></svg>
        info@bramblewoodcardco.com
      </p>
      <p class="contact__line">
        <svg class="contact__icon" viewBox="0 0 10 10" aria-hidden="true"><circle cx="5" cy="5" r="4.5" fill="var(--brand-blue)"/><path d="M0.5 5 H9.5 M5 0.5 V9.5" stroke="#fff" stroke-width="0.7"/></svg>
        www.bramblewoodcardco.com
      </p>
    </div>
  </section>

  <section class="card card--back" aria-label="Business card back">
    <div class="brand">
      <span class="brand__mark"></span>
      <span class="brand__name">Bramblewood Card Company</span>
    </div>
  </section>

</main>
</body>
</html>
```